Brightmill Data Works

Our company is about IT hardwares and IT solutions. IT hardware such as PC, RAMS, storage and servers. IT solutions such as project management, BA. We are also selling new technology too.

Target Market(s)

Consumer, Small to Medium Business, Corporate

Requirements
Must have
• The business card must have the following:
• Name:
• Title:
• Contact Number:
• Email address:
• Website:
• Color: Must match the logo color upgrade

```html
<!DOCTYPE html>
<html lang="en">
<head>
<meta charset="utf-8">
<title>Brightmill Data Works – Business Card</title>
<link rel="stylesheet" href="https://fonts.googleapis.com/css2?family=Roboto:wght@400;700&display=swap">
<style>
  :root {
    --canvas: #2a2a2b;
    --card-dark: #434343;
    --card-light: #f1f1f1;
    --accent: #c97a2a;
    --accent-deep: #b45e22;
    --accent-light: #d38d34;
    --text-light: #ffffff;
    --text-dark: #3d3d3d;
  }
  * { box-sizing: border-box; margin: 0; padding: 0; }
  html, body {
    width: 1200px; height: 923px; overflow: hidden;
    background: var(--canvas);
    font-family: "Roboto", Arial, sans-serif;
  }
  .canvas {
    width: 1200px; height: 923px;
    display: flex; flex-direction: column; align-items: center; justify-content: center; gap: 44px;
  }
  .card {
    position: relative; width: 640px; height: 366px; overflow: hidden;
    border-radius: 3px;
  }
  /* Front */
  .card-front { background: var(--card-dark); }
  .card-front .shape { position: absolute; inset: 0; }
  .brand-block {
    position: absolute; left: 40px; top: 132px; width: 280px;
    display: flex; align-items: center; gap: 12px;
  }
  .brand-mark { width: 20px; height: 20px; background: var(--accent); flex: none; }
  .brand-name {
    color: var(--text-dark); font-weight: 700; font-size: 28px; line-height: 1.08;
    letter-spacing: 0.5px; text-transform: uppercase;
  }
  .person {
    position: absolute; right: 40px; top: 40px; text-align: right;
  }
  .person-name { color: var(--text-light); font-size: 22px; letter-spacing: 0.5px; }
  .person-title { color: var(--accent); font-size: 18px; letter-spacing: 0.5px; margin-top: 2px; }
  .contacts {
    position: absolute; right: 40px; bottom: 46px; list-style: none;
    display: flex; flex-direction: column; gap: 8px;
  }
  .contact {
    display: flex; align-items: center; justify-content: flex-end; gap: 10px;
    color: var(--text-light); font-size: 16px;
  }
  .contact-icon {
    width: 20px; height: 20px; background: var(--accent);
    display: flex; align-items: center; justify-content: center;
  }
  .contact-icon svg { width: 13px; height: 13px; }
  /* Back */
  .card-back {
    background: linear-gradient(200deg, var(--accent-deep) 0%, var(--accent) 55%, var(--accent-light) 100%);
    display: flex; align-items: center; justify-content: center; gap: 18px;
  }
  .card-back .brand-mark { width: 34px; height: 34px; background: var(--text-light); }
  .card-back .brand-name { color: var(--text-light); font-size: 40px; }
</style>
</head>
<body>
<main class="canvas">
  <section class="card card-front" aria-label="Business card front">
    <svg class="shape" viewBox="0 0 640 366" preserveAspectRatio="none" aria-hidden="true">
      <path d="M0,0 H330 Q400,183 340,366 H0 Z" fill="var(--card-light)"/>
      <path d="M0,0 H324 Q394,183 334,366 H0 Z" fill="var(--accent)"/>
      <path d="M0,0 H312 Q380,183 322,366 H0 Z" fill="var(--card-light)"/>
    </svg>
    <div class="brand-block">
      <span class="brand-mark"></span>
      <p class="brand-name">Brightmill<br>Data Works</p>
    </div>
    <div class="person">
      <p class="person-name">MAREN HOLT</p>
      <p class="person-title">MANAGER</p>
    </div>
    <ul class="contacts">
      <li class="contact">+1-555-014-2287
        <span class="contact-icon"><svg viewBox="0 0 24 24"><path fill="#fff" d="M6.6 10.8a15 15 0 0 0 6.6 6.6l2.2-2.2c.3-.3.7-.4 1-.2 1.1.4 2.3.6 3.6.6.6 0 1 .4 1 1V20c0 .6-.4 1-1 1A17 17 0 0 1 3 4c0-.6.4-1 1-1h3.5c.6 0 1 .4 1 1 0 1.3.2 2.5.6 3.6.1.3 0 .7-.2 1z"/></svg></span>
      </li>
      <li class="contact">maren@brightmill.com
        <span class="contact-icon"><svg viewBox="0 0 24 24"><rect x="2" y="5" width="20" height="14" fill="none" stroke="#fff" stroke-width="2"/><path d="M2 5l10 8 10-8" fill="none" stroke="#fff" stroke-width="2"/></svg></span>
      </li>
      <li class="contact">www.brightmill.com
        <span class="contact-icon"><svg viewBox="0 0 24 24" fill="none" stroke="#fff" stroke-width="2"><circle cx="12" cy="12" r="9"/><path d="M3 12h18M12 3c3 3 3 15 0 18M12 3c-3 3-3 15 0 18"/></svg></span>
      </li>
    </ul>
  </section>

  <section class="card card-back" aria-label="Business card back">
    <span class="brand-mark"></span>
    <p class="brand-name">Brightmill<br>Data Works</p>
  </section>
</main>
</body>
</html>
```